Stationery Design Project for Nimbora, Chicago

Nimbora, a street parking application which helps car drivers find a street parking spot by offering an ideal path along which to look for parking. This path is calculated by our algorithm based on data (e.g. historical data, baseball games schedule, etc.). Along this path the driver will find a spot and will also save 70% of the search time. Customer we target is reg. between 21 and 45 yo.

We envision something young, fresh, bright and original. Slightly abstract maybe. It should represent the idea and elements of finding street parking in the city, e.g. car(s), parking spot, people, city, etc. (just ideas!).

Logo is attached.

Requirement:
- Business Cards (2 Sided Full Color CMYK)
- Letterhead (1 Sided Full Color CMYK)
- Envelope (1 Sided Full Color CMYK)
- Sticker (1 Sided Full Color CMYK), round with a 2inch diameter.

Reason: We're starting to get more and more designs and need more time to look into all of them. Very exciting!! Thanks to everybody!

Hi all, we're in the process of selecting our favs. Though choices!!! Really good submissions. Will keep you posted and sorry for the delay.

Target Market(s)

Car drivers and owners between 21 and 45

Industry/Entity Type

Parking

Requirements
Must have
• Sticker should be round and include company URL nimbora.com and the new logo which we will attach soon.
Should not have
• Should not be too serious or boring.

```html
<!DOCTYPE html>
<html lang="en">
<head>
<meta charset="utf-8">
<title>Nimbora — Business Cards</title>
<link href="https://fonts.googleapis.com/css2?family=Open+Sans:wght@400;600;700&display=swap" rel="stylesheet">
<style>
  :root {
    --page-bg: #e6e6e6;
    --card-bg: #ffffff;
    --ink-dark: #1f1f1f;
    --ink-mid: #555555;
    --ink-soft: #4a4a4a;
    --brand-blue: #1f5fd0;
    --brand-blue-deep: #123f9a;
    --ring: #e2e6ec;
  }
  * { box-sizing: border-box; margin: 0; padding: 0; }
  html, body {
    width: 954px; height: 1200px; overflow: hidden;
    background: var(--page-bg);
    font-family: "Open Sans", Arial, sans-serif;
  }
  .canvas { position: relative; width: 954px; height: 1200px; }
  .card {
    position: absolute; left: 75px; width: 798px; height: 456px;
    background: var(--card-bg); border-radius: 28px;
    box-shadow: 0 6px 14px rgba(0,0,0,0.18);
  }
  .card--front { top: 110px; }
  .card--back { top: 650px; }

  .brand-mark {
    position: absolute; border-radius: 50%;
    background: radial-gradient(circle at 40% 35%, var(--brand-blue), var(--brand-blue-deep));
  }
  .card--front .brand-mark {
    left: 103px; top: 51px; width: 230px; height: 230px;
    box-shadow: 0 0 0 14px var(--ring);
  }
  .card--back .brand-mark {
    left: 133px; top: 163px; width: 98px; height: 98px;
    box-shadow: 0 0 0 6px var(--ring);
  }
  .brand-name {
    position: absolute; color: var(--ink-dark); font-weight: 600;
    letter-spacing: 1px; line-height: 1;
  }
  .card--front .brand-name { left: 471px; top: 28px; font-size: 62px; }
  .card--back .brand-name { left: 254px; top: 151px; font-size: 112px; }

  .address {
    position: absolute; left: 72px; top: 372px; width: 300px;
    text-align: center; color: var(--ink-mid); font-size: 19px; line-height: 27px;
  }
  .person { position: absolute; left: 472px; top: 206px; color: var(--ink-mid); }
  .person__name { font-size: 24px; font-weight: 700; line-height: 30px; }
  .person__title { font-size: 19px; font-weight: 700; line-height: 26px; }

  .contacts { position: absolute; left: 472px; top: 296px; list-style: none; }
  .contacts li {
    display: flex; align-items: center; height: 32px;
    color: var(--ink-soft); font-size: 19px;
  }
  .contacts svg { width: 16px; height: 16px; margin: 0 9px 0 9px; fill: var(--ink-soft); }

  .web-line {
    position: absolute; left: 0; right: 0; top: 380px;
    text-align: center; color: var(--ink-mid); font-size: 19px;
  }
  .web-line b { font-weight: 700; }
  .web-line .sep { margin: 0 8px; }
</style>
</head>
<body>
<main class="canvas">
  <section class="card card--front">
    <div class="brand-mark"></div>
    <div class="brand-name">Nimbora</div>
    <p class="address">City Name, Street Name<br>State Name, Country Code</p>
    <div class="person">
      <p class="person__name">Your Name</p>
      <p class="person__title">Designation</p>
    </div>
    <ul class="contacts">
      <li><svg viewBox="0 0 16 16" aria-hidden="true"><path d="M2 5c0-2 2-3 6-3s6 1 6 3v1h-3V5H5v1H2z M4 8h8l2 6H2z"/></svg>123-456-7890</li>
      <li><svg viewBox="0 0 16 16" aria-hidden="true"><path d="M4 1h8v4H4z M1 6h14v6h-3v3H4v-3H1z"/></svg>123-456-7890</li>
      <li><svg viewBox="0 0 16 16" aria-hidden="true"><path d="M1 4h14v9H1z" fill="none" stroke="#4a4a4a" stroke-width="1.6"/><path d="M1 4l7 5 7-5" fill="none" stroke="#4a4a4a" stroke-width="1.6"/></svg>name@website.com</li>
      <li><svg viewBox="0 0 16 16" aria-hidden="true"><circle cx="8" cy="8" r="6.5"/></svg>www.website.com</li>
    </ul>
  </section>

  <section class="card card--back">
    <div class="brand-mark"></div>
    <div class="brand-name">Nimbora</div>
    <p class="web-line"><b>e</b> : name@website.com <span class="sep">|</span> <b>w</b> : www.website.com</p>
  </section>
</main>
</body>
</html>
```